Halvern Roofing & Waterproofing HOA & Commercial Roofing Specialists

FRONT COVER (Panel 1)
Halvern Roofing & Waterproofing
HOA & Commercial Roofing Specialists
Protecting Communities.
Preserving Property Value.
Delivering Long-Term Solutions.
📍 Serving Orange County & Surrounding Areas
INSIDE LEFT PANEL (Panel 2)
Who We Are
Halvern Roofing & Waterproofing is a trusted HOA and commercial roofing specialist serving Orange County and surrounding areas. We understand the unique needs of homeowner associations, property managers, and commercial properties—delivering reliable service, clear communication, and long-lasting results.
✔ HOA-Focused Expertise
✔ Licensed & Insured
✔ Emergency Response Available
✔ Quality Workmanship You Can Trust
INSIDE MIDDLE PANEL (Panel 3)
Roofing Services
HOA & Commercial Roofing
• Emergency roof tarping & repairs — Starting at $550
• Small & large roof repairs
• Chimney cap and spark arrestor repairs
• Preventative roof maintenance
• Roof cleaning
• Full roof replacement
We work on all roof types:
✔ Flat Roofs (Torch down, TPO, & PVC)
✔ Tile Roofs (Clay tiles, concrete tiles, and more)
✔ Shingle Roofs - KOV certified contractor
• Coating (silicone or acrylic)
No matter the size or system—we’ve got you covered.
INSIDE RIGHT PANEL (Panel 4)
Gutter Services
• Small & large gutter repairs
• Gutter cleaning & maintenance
• New gutter installation & replacement
Proper drainage protects your building—let us handle it.
BACK LEFT PANEL (Panel 5)
Deck/Balcony Waterproofing Services
• Balcony/deck maintenance
• Deck resurfacing
• Small & large deck repairs
• Full deck reconstruction
Specialized waterproofing solutions to keep decks safe, compliant, and durable.
BACK COVER (Panel 6)
Why Choose Halvern?
✔ HOA & Commercial Specialists
✔ Fully Licensed & Insured
✔ Reliable Scheduling
✔ Clear Communication
✔ Quality Materials & Craftsmanship
License Information:
C-39 Roofing Contractor
General B Contractor
License #4630257
📍 Office Location:
14 Dunmore Street, Suite J Irvine, CA 92618
📞 Contact us today for a consultation
949-372-6104 or rfp@halvernroofing.com
🌐 Serving Orange County & surrounding areas
- Gotham

```html
<!DOCTYPE html>
<html lang="en">
<head>
<meta charset="utf-8">
<title>Halvern Roofing &amp; Waterproofing – Trifold Brochure</title>
<link rel="stylesheet" href="https://fonts.googleapis.com/css2?family=Montserrat:wght@400;500;600;700;800;900&display=swap">
<style>
  :root{
    --blue:#18a0ea;
    --blue-soft:#6cc3f2;
    --ink:#161616;
    --dark:#232323;
    --dark-2:#2e2e2e;
    --white:#ffffff;
    --paper:#ececec;
    --muted:#cfcfcf;
  }
  html,body{margin:0;padding:0}
  body{
    width:1200px;height:2823px;overflow:hidden;
    background:var(--paper);
    font-family:"Montserrat",Arial,sans-serif;
    position:relative;
  }
  .spread{position:absolute;left:50px;width:1100px;height:852px;
    box-shadow:0 18px 40px rgba(0,0,0,.18);background:var(--white)}
  .spread--outside{top:519px}
  .spread--inside{top:1451px}
  .spread svg{display:block;width:1100px;height:852px}
  .f-blue{fill:var(--blue)} .f-ink{fill:var(--ink)} .f-white{fill:var(--white)}
  .f-dark{fill:var(--dark)} .f-dark2{fill:var(--dark-2)}
  text{font-family:"Montserrat",Arial,sans-serif}
  .t-title{font-weight:800;font-size:17px}
  .t-cap{font-weight:700;font-size:10.5px}
  .t-pill{font-weight:600;font-size:9px}
  .t-body{font-weight:500;font-size:11px}
  .t-bold{font-weight:700}
  .t-xb{font-weight:800}
  .t-black{font-weight:900}
</style>
</head>
<body>

<!-- OUTSIDE SPREAD: deck services / back cover / front cover -->
<section class="spread spread--outside">
<svg viewBox="0 0 906 702" xmlns="http://www.w3.org/2000/svg">
  <defs>
    <linearGradient id="gDeck" x1="0" y1="0" x2="0" y2="1"><stop offset="0" stop-color="#b87a5a"/><stop offset=".35" stop-color="#8f9aa2"/><stop offset="1" stop-color="#6f7a82"/></linearGradient>
    <linearGradient id="gDeck2" x1="0" y1="0" x2="0" y2="1"><stop offset="0" stop-color="#a36b52"/><stop offset=".3" stop-color="#7d8583"/><stop offset="1" stop-color="#5f6766"/></linearGradient>
    <linearGradient id="gRoofs" x1="0" y1="0" x2="1" y2="1"><stop offset="0" stop-color="#8a8f88"/><stop offset=".5" stop-color="#5c6158"/><stop offset="1" stop-color="#9aa39e"/></linearGradient>
    <linearGradient id="gTileRoof" x1="0" y1="0" x2="1" y2="1"><stop offset="0" stop-color="#b48a78"/><stop offset=".55" stop-color="#6f747c"/><stop offset="1" stop-color="#3e4550"/></linearGradient>
    <linearGradient id="gCover" x1="0" y1="0" x2="0" y2="1"><stop offset="0" stop-color="#3b8ee0"/><stop offset=".3" stop-color="#8fc3ea"/><stop offset=".55" stop-color="#4f6b4a"/><stop offset=".8" stop-color="#8a5444"/><stop offset="1" stop-color="#7a6a6a"/></linearGradient>
    <linearGradient id="gDarkPanel" x1="0" y1="0" x2="0" y2="1"><stop offset="0" stop-color="#2a2a2a"/><stop offset="1" stop-color="#1c1c1c"/></linearGradient>
  </defs>

  <!-- Panel: Deck & Balcony Services -->
  <g class="panel panel--deck">
    <rect x="0" y="0" width="303" height="702" class="f-white"/>
    <polygon class="f-blue" points="0,0 362,0 0,352"/>
    <polygon class="f-white" points="22,26 330,26 303,52 303,702 0,702 0,330 22,308"/>
    <text x="41" y="50" class="t-title f-ink">Deck &amp; Balcony Services</text>

    <rect x="35" y="67" width="225" height="129" rx="7" class="f-ink"/>
    <rect x="35" y="67" width="225" height="103" rx="7" fill="url(#gDeck)" role="img" aria-label="Photo of a waterproofed balcony deck"/>
    <text x="147.5" y="188" text-anchor="middle" class="t-cap f-white">Balcony &amp; deck maintenance</text>

    <rect x="35" y="202" width="225" height="129" rx="7" class="f-blue"/>
    <rect x="35" y="202" width="225" height="103" rx="7" fill="url(#gDeck2)" role="img" aria-label="Photo of a freshly resurfaced deck"/>
    <text x="147.5" y="323" text-anchor="middle" class="t-cap f-white">Deck resurfacing</text>

    <rect x="35" y="337" width="225" height="129" rx="7" class="f-ink"/>
    <rect x="35" y="337" width="225" height="103" rx="7" fill="url(#gRoofs)" role="img" aria-label="Aerial photo of decks under repair"/>
    <text x="147.5" y="458" text-anchor="middle" class="t-cap f-white">Small &amp; large deck repairs</text>

    <rect x="35" y="472" width="225" height="128" rx="7" class="f-blue"/>
    <rect x="35" y="472" width="225" height="102" rx="7" fill="url(#gTileRoof)" role="img" aria-label="Photo of a deck reconstruction beside a tile roof"/>
    <text x="147.5" y="592" text-anchor="middle" class="t-cap f-white">Full deck reconstruction</text>

    <text x="37" y="627" class="t-bold f-ink" font-size="10.5">Specialized waterproofing solutions to</text>
    <rect x="35" y="638" width="94" height="15" rx="2" class="f-ink"/>
    <text x="82" y="649" text-anchor="middle" class="t-bold f-white" font-size="9.5">Keep decks safe</text>
    <rect x="133" y="638" width="61" height="15" rx="2" class="f-ink"/>
    <text x="163.5" y="649" text-anchor="middle" class="t-bold f-white" font-size="9.5">Compliant</text>
    <text x="204" y="651" text-anchor="middle" class="t-xb f-ink" font-size="13">&amp;</text>
    <rect x="215" y="638" width="52" height="15" rx="2" class="f-ink"/>
    <text x="241" y="649" text-anchor="middle" class="t-bold f-white" font-size="9.5">Durable</text>
  </g>

  <!-- Panel: Back cover -->
  <g class="panel panel--back">
    <polygon points="362,0 604,0 604,702 303,702 303,52" fill="url(#gDarkPanel)"/>
    <text x="454" y="50" text-anchor="middle" class="t-title f-white">Why Choose Halvern?</text>
    <g class="reasons">
      <rect x="347" y="62" width="206" height="20" rx="5" class="f-white"/>
      <circle cx="359" cy="72" r="7" fill="none" stroke="#161616" stroke-width="1.5"/>
      <text x="372" y="75.5" class="t-pill f-ink">HOA &amp; Commercial Specialists</text>
      <rect x="347" y="87" width="206" height="20" rx="5" class="f-white"/>
      <circle cx="359" cy="97" r="7" fill="none" stroke="#161616" stroke-width="1.5"/>
      <text x="372" y="100.5" class="t-pill f-ink">Fully Licensed &amp; Insured</text>
      <rect x="347" y="112" width="206" height="20" rx="5" class="f-white"/>
      <circle cx="359" cy="122" r="7" fill="none" stroke="#161616" stroke-width="1.5"/>
      <text x="372" y="125.5" class="t-pill f-ink">Reliable Scheduling</text>
      <rect x="347" y="137" width="206" height="20" rx="5" class="f-white"/>
      <circle cx="359" cy="147" r="7" fill="none" stroke="#161616" stroke-width="1.5"/>
      <text x="372" y="150.5" class="t-pill f-ink">Clear Communication</text>
      <rect x="347" y="162" width="206" height="20" rx="5" class="f-white"/>
      <circle cx="359" cy="172" r="7" fill="none" stroke="#161616" stroke-width="1.5"/>
      <text x="372" y="175.5" class="t-pill f-ink">Quality Materials &amp; Craftsmanship</text>
    </g>
    <text x="454" y="210" text-anchor="middle" class="t-xb f-blue" font-size="15.5">License Information</text>
    <text x="454" y="231" text-anchor="middle" class="t-bold f-white" font-size="11">C-39 Roofing Contractor</text>
    <text x="454" y="250" text-anchor="middle" class="t-bold f-white" font-size="11">General B Contractor</text>

    <rect x="344" y="270" width="219" height="432" class="f-white"/>
    <rect x="397" y="258" width="114" height="17" rx="8.5" class="f-blue"/>
    <text x="454" y="270.5" text-anchor="middle" class="t-bold f-white" font-size="11">License #4630257</text>

    <text x="454" y="313" text-anchor="middle" class="t-black f-ink" font-size="26" letter-spacing="1">HALVERN</text>
    <text x="454" y="333" text-anchor="middle" class="f-ink" font-weight="500" font-size="8">ROOFING &amp; WATERPROOFING</text>
    <text x="454" y="374" text-anchor="middle" class="t-bold f-blue" font-size="13.5">OFFICE LOCATION</text>
    <path class="f-blue" d="M454 383c-5 0-8.5 3.6-8.5 8.3 0 6 8.5 13 8.5 13s8.5-7 8.5-13c0-4.7-3.5-8.3-8.5-8.3zm0 11.5a3.2 3.2 0 110-6.4 3.2 3.2 0 010 6.4z"/>
    <text x="454" y="419" text-anchor="middle" class="t-body f-ink">14 Dunmore Street,</text>
    <text x="454" y="432" text-anchor="middle" class="t-body f-ink">Suite J Irvine, CA 92618</text>
    <rect x="372" y="448" width="165" height="35" rx="6" class="f-ink"/>
    <text x="454" y="462" text-anchor="middle" class="t-bold f-blue" font-size="11.5">CONTACT US TODAY</text>
    <text x="454" y="476" text-anchor="middle" class="t-bold f-white" font-size="11.5">FOR A CONSULTATION</text>
    <circle cx="454" cy="500" r="9" class="f-blue"/>
    <path d="M450.5 495.5l2 -.5 1.2 2.6-1.3 1c.6 1.3 1.6 2.3 2.9 2.9l1-1.3 2.6 1.2-.5 2c-4.5 0-7.9-3.4-7.9-7.9z" class="f-white"/>
    <text x="454" y="526" text-anchor="middle" class="t-bold f-ink" font-size="12">949-372-6104</text>
    <circle cx="454" cy="544" r="9" class="f-blue"/>
    <rect x="449" y="540.5" width="10" height="7" rx="1" class="f-white"/>
    <path d="M449 541l5 3.5 5-3.5" fill="none" stroke="#18a0ea" stroke-width="1"/>
    <text x="454" y="566" text-anchor="middle" class="t-body f-ink" font-size="11.5">rfp@halvernroofing.com</text>

    <rect x="363" y="582" width="181" height="85" class="f-blue"/>
    <rect x="370" y="590" width="52" height="70" rx="4" fill="#6cc3f2" opacity=".6" role="img" aria-label="Map of Orange County"/>
    <text x="418" y="612" class="t-bold f-white" font-size="11">Serving Orange</text>
    <text x="418" y="626" class="t-bold f-white" font-size="11">County &amp;</text>
    <text x="418" y="640" class="t-bold f-white" font-size="11">surrounding areas</text>
  </g>
  <polygon class="f-blue" points="262,702 346,702 346,618"/>

  <!-- Panel: Front cover -->
  <g class="panel panel--cover">
    <rect x="604" y="0" width="302" height="702" class="f-white"/>
    <polygon points="604,0 906,0 906,470 711,318 604,420" fill="url(#gCover)" role="img" aria-label="Photo of roofers working on a tile roof with palm trees behind"/>
    <polygon class="f-blue" points="562,468 711,318 906,470 906,522 711,372 604,478 604,468"/>
    <text x="755" y="65" text-anchor="middle" class="t-black f-ink" font-size="34" letter-spacing="1">HALVERN</text>
    <text x="755" y="92" text-anchor="middle" class="f-ink" font-weight="500" font-size="10">ROOFING &amp; WATERPROOFING</text>

    <g class="f-ink">
      <rect x="689" y="372" width="22" height="22"/><rect x="714" y="372" width="22" height="22"/>
      <rect x="689" y="397" width="22" height="22"/><rect x="714" y="397" width="22" height="22"/>
    </g>
    <text x="647" y="454" class="t-black f-blue" font-size="22">HOA &amp;</text>
    <text x="647" y="478" class="t-black f-blue" font-size="22">COMMERCIAL</text>
    <text x="647" y="508" class="t-black f-ink" font-size="29">ROOFING</text>
    <text x="647" y="532" class="t-black f-ink" font-size="21">SPECIALISTS</text>

    <g class="pillars">
      <circle cx="663" cy="558" r="13" class="f-blue"/><circle cx="663" cy="558" r="11" class="f-ink"/>
      <circle cx="663" cy="558" r="5" fill="none" stroke="#fff" stroke-width="1.5"/>
      <text x="647" y="586" class="t-bold f-ink" font-size="9" fill-opacity=".85">Protecting</text>
      <text x="647" y="597" class="t-bold f-ink" font-size="9" fill-opacity=".85">Communities</text>
      <circle cx="748" cy="558" r="13" class="f-blue"/><circle cx="748" cy="558" r="11" class="f-ink"/>
      <circle cx="748" cy="558" r="5" fill="none" stroke="#fff" stroke-width="1.5"/>
      <text x="732" y="586" class="t-bold f-ink" font-size="9" fill-opacity=".85">Preserving</text>
      <text x="732" y="597" class="t-bold f-ink" font-size="9" fill-opacity=".85">Property</text>
      <text x="732" y="608" class="t-bold f-ink" font-size="9" fill-opacity=".85">Value</text>
      <circle cx="822" cy="558" r="13" class="f-blue"/><circle cx="822" cy="558" r="11" class="f-ink"/>
      <circle cx="822" cy="558" r="5" fill="none" stroke="#fff" stroke-width="1.5"/>
      <text x="806" y="586" class="t-bold f-ink" font-size="9" fill-opacity=".85">Delivering</text>
      <text x="806" y="597" class="t-bold f-ink" font-size="9" fill-opacity=".85">Long-Term</text>
      <text x="806" y="608" class="t-bold f-ink" font-size="9" fill-opacity=".85">Solutions</text>
    </g>
    <path class="f-blue" d="M652 633c-4 0-7 3-7 6.8 0 5 7 10.7 7 10.7s7-5.7 7-10.7c0-3.8-3-6.8-7-6.8zm0 9.3a2.6 2.6 0 110-5.2 2.6 2.6 0 010 5.2z"/>
    <rect x="660" y="634" width="208" height="18" rx="3" class="f-ink"/>
    <text x="666" y="646.5" class="t-bold f-white" font-size="7.6">Serving Orange County &amp; Surrounding Areas</text>
  </g>
</svg>
</section>

<!-- INSIDE SPREAD: who we are / roofing services / gutter services -->
<section class="spread spread--inside">
<svg viewBox="0 0 906 702" xmlns="http://www.w3.org/2000/svg">
  <defs>
    <linearGradient id="gFlatRoof" x1="0" y1="0" x2="1" y2="1"><stop offset="0" stop-color="#6f8aa0"/><stop offset=".4" stop-color="#d9dde0"/><stop offset="1" stop-color="#9aa2a8"/></linearGradient>
    <linearGradient id="gTile" x1="0" y1="0" x2="1" y2="1"><stop offset="0" stop-color="#9b7362"/><stop offset="1" stop-color="#5a5f66"/></linearGradient>
    <linearGradient id="gTopView" x1="0" y1="0" x2="0" y2="1"><stop offset="0" stop-color="#6b7a58"/><stop offset="1" stop-color="#a0664e"/></linearGradient>
    <linearGradient id="gWhiteRoof" x1="0" y1="0" x2="0" y2="1"><stop offset="0" stop-color="#8fb6d8"/><stop offset=".5" stop-color="#dfe4e7"/><stop offset="1" stop-color="#a7aeb3"/></linearGradient>
    <linearGradient id="gSolar" x1="0" y1="0" x2="0" y2="1"><stop offset="0" stop-color="#7e9ab8"/><stop offset="1" stop-color="#4a5468"/></linearGradient>
    <linearGradient id="gGutter1" x1="0" y1="0" x2="1" y2="1"><stop offset="0" stop-color="#a8705a"/><stop offset="1" stop-color="#7c6a62"/></linearGradient>
    <linearGradient id="gGutter2" x1="0" y1="0" x2="1" y2="1"><stop offset="0" stop-color="#3f6a3a"/><stop offset="1" stop-color="#8e8e8a"/></linearGradient>
    <linearGradient id="gGutter3" x1="0" y1="0" x2="1" y2="1"><stop offset="0" stop-color="#8a8270"/><stop offset="1" stop-color="#44484e"/></linearGradient>
    <linearGradient id="gAerial" x1="0" y1="0" x2="1" y2="1"><stop offset="0" stop-color="#9aa5ab"/><stop offset="1" stop-color="#5f6a70"/></linearGradient>
    <linearGradient id="gMidDark" x1="0" y1="0" x2="0" y2="1"><stop offset="0" stop-color="#2c2c2c"/><stop offset="1" stop-color="#1e1e1e"/></linearGradient>
  </defs>

  <!-- Panel: Who We Are -->
  <g class="panel panel--about">
    <rect x="0" y="0" width="303" height="702" class="f-blue"/>
    <polygon points="0,482 303,470 303,702 0,702" fill="url(#gWhiteRoof)" role="img" aria-label="Photo of a white coated flat commercial roof"/>
    <polygon class="f-blue" points="250,702 303,648 303,702"/>
    <text x="35" y="52" class="t-xb f-ink" font-size="22">Who We Are</text>
    <text x="37" y="70" class="f-white" font-weight="500" font-size="8.6">Halvern Roofing &amp; Waterproofing is a trusted HOA</text>
    <text x="37" y="81" class="f-white" font-weight="500" font-size="8.6">and commercial roofing specialist serving Orange</text>
    <text x="37" y="92" class="f-white" font-weight="500" font-size="8.6">County and surrounding areas.</text>
    <text x="37" y="114" class="t-bold f-white" font-size="8.6">We understand the unique needs of</text>
    <g class="needs">
      <rect x="35" y="128" width="211" height="19" rx="4" class="f-white"/><circle cx="45" cy="137.5" r="3.5" class="f-ink"/>
      <text x="53" y="140.5" class="t-pill f-ink" font-size="8.5">Homeowner associations</text>
      <rect x="35" y="153" width="211" height="19" rx="4" class="f-white"/><circle cx="45" cy="162.5" r="3.5" class="f-ink"/>
      <text x="53" y="165.5" class="t-pill f-ink" font-size="8.5">Property managers</text>
      <rect x="35" y="178" width="211" height="19" rx="4" class="f-white"/><circle cx="45" cy="187.5" r="3.5" class="f-ink"/>
      <text x="53" y="190.5" class="t-pill f-ink" font-size="8.5">Commercial properties delivering</text>
      <rect x="35" y="203" width="211" height="19" rx="4" class="f-white"/><circle cx="45" cy="212.5" r="3.5" class="f-ink"/>
      <text x="53" y="215.5" class="t-pill f-ink" font-size="8.5">Reliable service</text>
      <rect x="35" y="228" width="211" height="19" rx="4" class="f-white"/><circle cx="45" cy="237.5" r="3.5" class="f-ink"/>
      <text x="53" y="240.5" class="t-pill f-ink" font-size="8.5">Clear communication</text>
      <rect x="35" y="253" width="211" height="19" rx="4" class="f-white"/><circle cx="45" cy="262.5" r="3.5" class="f-ink"/>
      <text x="53" y="265.5" class="t-pill f-ink" font-size="8.5">Long-lasting results.</text>
    </g>
    <g class="strengths">
      <rect x="37" y="285" width="104" height="80" rx="8" class="f-ink"/>
      <circle cx="89" cy="311" r="11" fill="none" stroke="#fff" stroke-width="1.5"/>
      <text x="89" y="342" text-anchor="middle" class="t-bold f-white" font-size="8.5">HOA-Focused</text>
      <text x="89" y="353" text-anchor="middle" class="t-bold f-white" font-size="8.5">Expertise</text>
      <rect x="149" y="285" width="104" height="80" rx="8" class="f-ink"/>
      <rect x="191" y="300" width="18" height="22" rx="2" fill="none" stroke="#fff" stroke-width="1.5"/>
      <path d="M195 312l3 3 7-7" fill="none" stroke="#fff" stroke-width="1.5"/>
      <text x="201" y="342" text-anchor="middle" class="t-bold f-white" font-size="8.5">Licensed &amp;</text>
      <text x="201" y="353" text-anchor="middle" class="t-bold f-white" font-size="8.5">Insured</text>
      <rect x="37" y="385" width="104" height="80" rx="8" class="f-ink"/>
      <circle cx="89" cy="408" r="11" fill="none" stroke="#fff" stroke-width="1.5"/>
      <path d="M89 401v8l5 3" fill="none" stroke="#fff" stroke-width="1.5"/>
      <text x="89" y="436" text-anchor="middle" class="t-bold f-white" font-size="8.5">Emergency</text>
      <text x="89" y="447" text-anchor="middle" class="t-bold f-white" font-size="8.5">Response</text>
      <text x="89" y="458" text-anchor="middle" class="t-bold f-white" font-size="8.5">Available</text>
      <rect x="149" y="385" width="104" height="80" rx="8" class="f-ink"/>
      <circle cx="201" cy="408" r="11" fill="none" stroke="#fff" stroke-width="1.5"/>
      <circle cx="201" cy="408" r="4" fill="none" stroke="#fff" stroke-width="1.5"/>
      <text x="201" y="436" text-anchor="middle" class="t-bold f-white" font-size="8.5">Quality</text>
      <text x="201" y="447" text-anchor="middle" class="t-bold f-white" font-size="8.5">Workmanship</text>
      <text x="201" y="458" text-anchor="middle" class="t-bold f-white" font-size="8.5">You Can Trust</text>
    </g>
  </g>

  <!-- Panel: Roofing Services -->
  <g class="panel panel--roofing">
    <rect x="303" y="0" width="301" height="702" fill="url(#gMidDark)"/>
    <polygon class="f-blue" points="262,0 630,0 566,74 330,74"/>
    <polygon class="f-ink" points="280,0 612,0 558,64 338,64"/>
    <g class="f-white">
      <rect x="322" y="53" width="5" height="5"/><rect x="328" y="53" width="5" height="5"/>
      <rect x="322" y="59" width="5" height="5"/><rect x="328" y="59" width="5" height="5"/>
    </g>
    <text x="452" y="44" text-anchor="middle" class="t-xb f-white" font-size="20">Roofing Services</text>
    <text x="454" y="110" text-anchor="middle" class="t-bold f-white" font-size="15.5">HOA &amp; Commercial Roofing</text>

    <rect x="343" y="140" width="104" height="150" rx="6" class="f-blue"/>
    <rect x="343" y="140" width="104" height="92" rx="6" fill="url(#gTile)" role="img" aria-label="Photo of a tile roof under emergency tarping"/>
    <text x="395" y="249" text-anchor="middle" class="t-bold f-white" font-size="11">Emergency</text>
    <text x="395" y="262" text-anchor="middle" class="t-bold f-white" font-size="11">roof tarping</text>
    <text x="395" y="275" text-anchor="middle" class="t-bold f-white" font-size="11">&amp; repairs</text>
    <circle cx="427" cy="136" r="16" class="f-white" stroke="#161616" stroke-width="1.5"/>
    <text x="427" y="131" text-anchor="middle" class="t-bold f-ink" font-size="4.5">STARTING AT</text>
    <text x="427" y="142" text-anchor="middle" class="t-xb f-ink" font-size="10">$550</text>

    <rect x="458" y="140" width="105" height="150" rx="6" class="f-blue"/>
    <rect x="458" y="140" width="105" height="92" rx="6" fill="url(#gTopView)" role="img" aria-label="Aerial photo of roof repairs on a residential complex"/>
    <text x="510" y="249" text-anchor="middle" class="t-bold f-white" font-size="11">Small &amp;</text>
    <text x="510" y="262" text-anchor="middle" class="t-bold f-white" font-size="11">large roof</text>
    <text x="510" y="275" text-anchor="middle" class="t-bold f-white" font-size="11">repairs</text>

    <rect x="343" y="297" width="104" height="150" rx="6" class="f-blue"/>
    <rect x="343" y="297" width="104" height="93" rx="6" fill="url(#gWhiteRoof)" role="img" aria-label="Photo of a maintained white flat roof"/>
    <text x="395" y="406" text-anchor="middle" class="t-bold f-white" font-size="11">Preventative</text>
    <text x="395" y="419" text-anchor="middle" class="t-bold f-white" font-size="11">roof</text>
    <text x="395" y="432" text-anchor="middle" class="t-bold f-white" font-size="11">maintenance</text>

    <rect x="458" y="297" width="105" height="150" rx="6" class="f-blue"/>
    <rect x="458" y="297" width="105" height="93" rx="6" fill="url(#gSolar)" role="img" aria-label="Photo of a fully replaced roof with solar panels"/>
    <text x="510" y="413" text-anchor="middle" class="t-bold f-white" font-size="11">Full roof</text>
    <text x="510" y="426" text-anchor="middle" class="t-bold f-white" font-size="11">replacement</text>

    <polygon class="f-blue" points="453,420 615,585 604,585 453,432 303,585 292,585"/>
    <polygon class="f-white" points="453,432 604,585 604,702 303,702 303,585"/>
    <g class="f-ink">
      <rect x="438" y="454" width="14" height="14"/><rect x="454" y="454" width="14" height="14"/>
      <rect x="438" y="470" width="14" height="14"/><rect x="454" y="470" width="14" height="14"/>
    </g>
    <text x="453" y="516" text-anchor="middle" class="t-xb f-blue" font-size="12.5">WE WORK ON</text>
    <text x="453" y="530" text-anchor="middle" class="t-xb f-blue" font-size="12.5">ALL ROOF TYPES</text>
    <g class="roof-types">
      <circle cx="380" cy="572" r="5" class="f-blue"/><path d="M377.5 572l2 2 3-3.5" fill="none" stroke="#fff" stroke-width="1.2"/>
      <text x="380" y="597" text-anchor="middle" class="t-xb f-ink" font-size="14">FLAT</text>
      <text x="380" y="613" text-anchor="middle" class="t-xb f-ink" font-size="14">ROOFS</text>
      <line x1="417" y1="565" x2="417" y2="616" stroke="#999" stroke-width="1"/>
      <circle cx="453" cy="572" r="5" class="f-blue"/><path d="M450.5 572l2 2 3-3.5" fill="none" stroke="#fff" stroke-width="1.2"/>
      <text x="453" y="597" text-anchor="middle" class="t-xb f-ink" font-size="14">TILE</text>
      <text x="453" y="613" text-anchor="middle" class="t-xb f-ink" font-size="14">ROOFS</text>
      <line x1="490" y1="565" x2="490" y2="616" stroke="#999" stroke-width="1"/>
      <circle cx="526" cy="572" r="5" class="f-blue"/><path d="M523.5 572l2 2 3-3.5" fill="none" stroke="#fff" stroke-width="1.2"/>
      <text x="526" y="597" text-anchor="middle" class="t-xb f-ink" font-size="14">SHINGLE</text>
      <text x="526" y="613" text-anchor="middle" class="t-xb f-ink" font-size="14">ROOFS</text>
    </g>
    <text x="453" y="647" text-anchor="middle" class="t-bold f-ink" font-size="11.5">No matter the size or system</text>
    <text x="453" y="661" text-anchor="middle" class="t-bold f-ink" font-size="11.5">we’ve got you covered.</text>
  </g>

  <!-- Panel: Gutter Services -->
  <g class="panel panel--gutters">
    <rect x="604" y="0" width="302" height="702" class="f-white"/>
    <polygon class="f-blue" points="630,0 640,0 604,40 604,30"/>
    <text x="644" y="52" class="t-title f-ink">Gutter Services</text>

    <rect x="641" y="63" width="226" height="129" rx="7" class="f-ink"/>
    <rect x="641" y="63" width="226" height="105" rx="7" fill="url(#gGutter1)" role="img" aria-label="Photo of workers repairing gutters on a tile roof"/>
    <text x="754" y="184" text-anchor="middle" class="t-cap f-white">Small &amp; large gutter repairs</text>

    <rect x="641" y="198" width="226" height="129" rx="7" class="f-ink"/>
    <rect x="641" y="198" width="226" height="105" rx="7" fill="url(#gGutter2)" role="img" aria-label="Photo of a cleaned gutter beside trees"/>
    <text x="754" y="319" text-anchor="middle" class="t-cap f-white">Gutter cleaning &amp; maintenance</text>

    <rect x="641" y="333" width="226" height="129" rx="7" class="f-ink"/>
    <rect x="641" y="333" width="226" height="105" rx="7" fill="url(#gGutter3)" role="img" aria-label="Photo of a new gutter being installed"/>
    <text x="754" y="454" text-anchor="middle" class="t-cap f-white">New gutter installation &amp; replacement</text>

    <text x="644" y="490" class="t-bold f-ink" font-size="13">Proper drainage protects your</text>
    <text x="644" y="506" class="t-bold f-ink" font-size="13">building—let us handle it.</text>

    <polygon points="604,545 906,520 906,702 604,702" fill="url(#gAerial)" role="img" aria-label="Aerial photo of a residential community"/>
    <polygon class="f-blue" points="604,545 775,702 740,702 604,582"/>
  </g>
</svg>
</section>

</body>
</html>
```